"Harbor Builders" is a residential building company and needs a new business card design and may re

We would like a redesign based on the existing logo, and would like to see a new font as well. We are bespoke home builders who build sustainable energy efficient homes.

Industry/Entity Type

Construction

Contact Information for Business Card

Business card size 40mm x 90mm

Colors

Designer to choose colors to be used in the design.

```html
<!DOCTYPE html>
<html lang="en">
<head>
<meta charset="utf-8">
<title>Harbor Builders – Business Card</title>
<link rel="stylesheet" href="https://fonts.googleapis.com/css2?family=Roboto:wght@400;500&family=Roboto+Condensed:wght@500&family=Open+Sans:wght@400;600&display=swap">
<style>
  :root {
    --lime: #b9d531;
    --ink: #231f20;
    --black: #111111;
    --paper: #f4f4f4;
    --text: #4a4a4a;
    --rule: #8a8a8a;
    --backdrop: #e6e3de;
  }
  * { margin: 0; padding: 0; box-sizing: border-box; }
  html, body { width: 1200px; height: 960px; overflow: hidden; }
  body {
    position: relative;
    background: var(--backdrop);
    font-family: "Roboto", Arial, sans-serif;
  }
  .card {
    position: absolute;
    width: 600px;
    height: 343px;
    box-shadow: 0 3px 10px rgba(0,0,0,0.25);
    overflow: hidden;
  }

  /* Front */
  .card-front { left: 302px; top: 129px; background: var(--paper); }
  .brand-mark {
    position: absolute;
    right: 56px;
    top: 48px;
    display: flex;
    align-items: center;
    gap: 12px;
  }
  .brand-square { width: 26px; height: 26px; background: var(--lime); }
  .brand-name {
    font-family: "Open Sans", Arial, sans-serif;
    font-weight: 600;
    font-size: 30px;
    color: var(--ink);
    letter-spacing: -0.3px;
  }
  .holder-name {
    position: absolute;
    left: 28px;
    top: 165px;
    font-family: "Roboto Condensed", Arial, sans-serif;
    font-weight: 500;
    font-size: 22px;
    color: var(--ink);
  }
  .name-rule {
    position: absolute;
    left: 28px;
    right: 30px;
    top: 197px;
    height: 1px;
    background: var(--rule);
  }
  .credentials {
    position: absolute;
    left: 30px;
    top: 206px;
    font-size: 14px;
    line-height: 18px;
    color: var(--text);
  }
  .contact-list {
    position: absolute;
    left: 30px;
    top: 248px;
    list-style: none;
    font-size: 14px;
    color: var(--text);
  }
  .contact-list li {
    display: flex;
    align-items: center;
    gap: 8px;
    height: 19.5px;
  }
  .contact-list svg { width: 13px; height: 13px; fill: var(--ink); flex: none; }
  .postal-address {
    position: absolute;
    right: 31px;
    top: 235px;
    text-align: right;
    font-style: normal;
    font-size: 14px;
    line-height: 18px;
    color: var(--text);
  }
  .postal-address .company { font-weight: 500; }
  .footer-band { position: absolute; left: 0; bottom: 0; width: 600px; height: 16px; }

  /* Back */
  .card-back { left: 299px; top: 488px; background: var(--lime); }
  .back-wordmark {
    position: absolute;
    right: 30px;
    top: 222px;
    font-family: "Open Sans", Arial, sans-serif;
    font-weight: 400;
    font-size: 44px;
    color: var(--ink);
    letter-spacing: -0.5px;
  }
  .back-web {
    position: absolute;
    right: 30px;
    top: 303px;
    font-size: 14px;
    color: var(--ink);
  }
</style>
</head>
<body>

<section class="card card-front" aria-label="Business card front">
  <div class="brand-mark">
    <span class="brand-square"></span>
    <span class="brand-name">harbor builders</span>
  </div>

  <h1 class="holder-name">DANIEL MORETTI</h1>
  <div class="name-rule"></div>

  <p class="credentials">Registration 40873<br>ABN: 52 204 613 778</p>

  <ul class="contact-list">
    <li>
      <svg viewBox="0 0 13 13" aria-hidden="true"><path d="M3 0h7a1 1 0 0 1 1 1v11a1 1 0 0 1-1 1H3a1 1 0 0 1-1-1V1a1 1 0 0 1 1-1zm.8 1.5v8.5h5.4V1.5z"/></svg>
      0400 123 987
    </li>
    <li>
      <svg viewBox="0 0 13 13" aria-hidden="true"><path d="M0 3h13v8H0zm1.3 1.2v.3l5.2 3.3 5.2-3.3v-.3zm0 1.7v3.9h10.4V5.9L6.5 9.2z"/></svg>
      daniel@harborbuilders.com.au
    </li>
    <li>
      <svg viewBox="0 0 13 13" aria-hidden="true"><circle cx="6.5" cy="6.5" r="6"/><path d="M3 4c1 0 2 1 2 2s-1 1-1 2 1 2 1 3M8 2c0 1 1 2 2 2s1 2 0 3-2 1-2 3" stroke="#f4f4f4" stroke-width="1.2" fill="none"/></svg>
      www.harborbuilders.com.au
    </li>
  </ul>

  <address class="postal-address">
    <span class="company">Harbor Builders Pty Ltd</span><br>
    PO Box 4120<br>
    Northgate<br>
    LPO Baywater WA 6099
  </address>

  <svg class="footer-band" viewBox="0 0 600 16" preserveAspectRatio="none" aria-hidden="true">
    <polygon points="0,0 391,0 386,16 0,16" fill="var(--black)"/>
    <polygon points="396,0 600,0 600,16 391,16" fill="var(--lime)"/>
  </svg>
</section>

<section class="card card-back" aria-label="Business card back">
  <p class="back-wordmark">harbor builders</p>
  <p class="back-web">www.harborbuilders.com.au</p>
</section>

</body>
</html>
```